Creative, fresh business card design for Ripplecraft Facades

We need a fresh, creative business card design for Ripplecraft Facades. We are the manufacturer of Ripplecraft Facades in Australia. Wall panels are 2400 x 1200mm panels made from MDF and feature 3D patterns on the face of the panel. The colours to be used are green, silver/grey and white RGB
Red 187
Green 207
Blue 65.

An idea is to possibly use a watermark of one of our designs as a background (like on the "Grids" design on the left hand side of page 2 of our brochure).

Target Market(s)

Interior designers, architects, builders and home renovators

Industry/Entity Type

Business

Contact Information for Business Card

Details to go on the card are:
Our logo (attached),
Slogan: "Decorative panels for interiors and exteriors",
Contact name,
Position,
Mobile phone number,
Business address,
Business phone,
Business fax,
Website and
Email address.

I have attached a few images of our panels and our brochure for reference.

The colours of the business card should feature our logo colours which are: RGB
Red 187
Green 207
Blue 65

Requirements
Must have
• Very modern fonts and design. Some of the designs shown especially the "Prisms" design which is a popular design.
Nice to have
• Creative but simple design. Very contemporary.
Should not have
• Anything ornate or old fashioned.

```html
<!DOCTYPE html>
<html lang="en">
<head>
<meta charset="utf-8">
<title>Ripplecraft Facades — Business Card</title>
<link rel="stylesheet" href="https://fonts.googleapis.com/css2?family=Arimo:wght@400;700&display=swap">
<style>
  :root {
    --green: #bbcf41;
    --grey: #8e9093;
    --grey-dark: #6d6e71;
    --ink: #3a3b3d;
    --white: #ffffff;
    --backdrop: #e9e9e7;
  }
  * { box-sizing: border-box; margin: 0; padding: 0; }
  html, body {
    width: 1200px; height: 987px; overflow: hidden;
    background: var(--backdrop);
    font-family: "Arimo", Arial, sans-serif;
  }
  .card {
    position: absolute; left: 292px; width: 616px; height: 350px;
    box-shadow: 0 4px 14px rgba(0,0,0,.18);
    overflow: hidden;
  }
  .card--front { top: 130px; background: var(--white); }
  .card--back { top: 506px; background: var(--grey); }

  .front__band { position: absolute; left: 0; top: 0; width: 100%; height: 12px; background: var(--green); }
  .front__foot { position: absolute; left: 0; bottom: 0; width: 100%; height: 13px; background: var(--grey); }

  .brand {
    position: absolute; left: 0; width: 100%;
    display: flex; flex-direction: column; align-items: center;
  }
  .card--front .brand { top: 70px; }
  .card--back .brand { top: 118px; }
  .brand__lockup { display: flex; align-items: center; gap: 14px; }
  .brand__square { width: 40px; height: 40px; background: var(--green); }
  .brand__name { font-size: 32px; font-weight: 400; letter-spacing: .5px; }
  .card--front .brand__name { color: var(--grey-dark); }
  .card--back .brand__name { color: var(--white); }
  .brand__tagline {
    margin-top: 18px; text-align: center;
    font-size: 13px; letter-spacing: 2.6px; line-height: 17px;
  }
  .card--front .brand__tagline { color: var(--grey); }
  .card--back .brand__tagline { color: var(--white); }

  .person {
    position: absolute; top: 242px; left: 0; width: 100%;
    text-align: center; white-space: nowrap;
  }
  .person__name { color: var(--green); font-weight: 700; font-size: 20px; }
  .person__role { color: var(--grey-dark); font-size: 16px; }
  .rule { position: absolute; top: 270px; left: 24px; right: 26px; height: 1px; background: var(--grey); }

  .contact {
    position: absolute; top: 282px; font-size: 15px; line-height: 21px; color: var(--ink);
  }
  .contact--address { left: 21px; }
  .contact--phones { left: 236px; }
  .contact--web { left: 400px; }
  .contact__row { display: flex; align-items: center; gap: 8px; }
  .contact__icon { width: 16px; height: 16px; fill: var(--green); }
</style>
</head>
<body>

<section class="card card--front">
  <div class="front__band"></div>
  <div class="brand">
    <div class="brand__lockup">
      <span class="brand__square"></span>
      <span class="brand__name">Ripplecraft Facades</span>
    </div>
    <p class="brand__tagline">decorative panels for<br>interiors &amp; landscapes</p>
  </div>

  <p class="person"><span class="person__name">MARA ELLISON - </span><span class="person__role">CEO&amp;Founder</span></p>
  <div class="rule"></div>

  <div class="contact contact--address">
    <p>214 Cedarfield Road</p>
    <p>Brookvale, NSW 2100</p>
  </div>
  <div class="contact contact--phones">
    <p class="contact__row">
      <svg class="contact__icon" viewBox="0 0 16 16" aria-hidden="true"><path d="M3.2 1l2.4 2.6-1.3 2.1c.9 2 2.4 3.6 4.5 4.6l2.1-1.3L13.5 11.4 12 14c-5.8-.4-10.2-4.9-10.6-10.7z"/></svg>
      (02) 5550 1827
    </p>
    <p class="contact__row">
      <svg class="contact__icon" viewBox="0 0 16 16" aria-hidden="true"><rect x="4" y="2" width="8" height="4"/><rect x="1" y="7" width="14" height="5" rx="1"/><rect x="4" y="12" width="8" height="2"/></svg>
      (02) 5550 3946
    </p>
  </div>
  <div class="contact contact--web">
    <p>mellison@ripplecraft.com</p>
    <p>www.ripplecraft.com</p>
  </div>
  <div class="front__foot"></div>
</section>

<section class="card card--back">
  <div class="brand">
    <div class="brand__lockup">
      <span class="brand__square"></span>
      <span class="brand__name">Ripplecraft Facades</span>
    </div>
    <p class="brand__tagline">decorative panels for<br>interiors &amp; landscapes</p>
  </div>
</section>

</body>
</html>
```